Bright Ledger Bookkeeping Business Cards

I need Business Cards for a new Bookkeeping Business on the Gold Coast, Australia called "Bright Ledger Bookkeeping". I do Bookkeeping & BAS's for small to medium size businesses onsite (ie I am Mobile) or in house (at my office). I also do one on one Training onsite with clients.
I am a Registered BAS Agent, Accredited Partner with Tallyo & Member of the LEDGRA Bookkeeping Circle. The Logo's I have uploaded all need to be on a white background.

Target Market(s)

Small to Medium Size Businesses

Industry/Entity Type

Business

Contact Information for Business Card

Bright Ledger Bookkeeping
Kim Farrow
PO Box 562 Marlin Reach, Qld 4388
ph 0488 615 903
email kim@kimfarrow-example.com.au

Font styles to use
Other font styles liked:
• Maybe something like Bradley Hand ITC

Requirements
Must have
• All logo's attached on white background.
• Should state that I am a Registered BAS Agent.
Nice to have
• I have a tag - "Bright Ledger - Clear Sums" if you think that works please add.
Should not have
• No brown, green or yellow please.

```html
<!DOCTYPE html>
<html lang="en">
<head>
<meta charset="utf-8">
<title>Bright Ledger Bookkeeping – Business Cards</title>
<link rel="stylesheet" href="https://fonts.googleapis.com/css2?family=Andika&display=swap">
<style>
  :root {
    --page-bg: #ecebe8;
    --card-bg: #ffffff;
    --maroon: #a5143f;
    --maroon-deep: #8e1236;
    --rule: #b33a5a;
    --badge: #c9c9c9;
    --fine: #6b6b6b;
  }
  * { margin: 0; padding: 0; box-sizing: border-box; }
  html, body { width: 1200px; height: 892px; overflow: hidden; }
  body {
    background: var(--page-bg);
    font-family: "Andika", sans-serif;
    font-weight: 400;
    color: var(--maroon);
    position: relative;
  }
  h1, h2 { font-weight: 400; }
  .card {
    position: absolute;
    top: 116px;
    width: 400px;
    height: 660px;
    background: var(--card-bg);
    box-shadow: 0 4px 14px rgba(0,0,0,0.12);
    overflow: hidden;
  }
  .card--front { left: 150px; }
  .card--back { left: 650px; }
  .card-shapes { position: absolute; inset: 0; }
  .card-shapes .tab { fill: var(--maroon-deep); }
  .card-shapes .rule { stroke: var(--rule); stroke-width: 1.2; }

  .holder-name {
    position: absolute; top: 82px; right: 60px;
    font-size: 30px;
  }
  .business-name {
    position: absolute; top: 196px; left: 40px; width: 320px;
    text-align: center;
    font-size: 38px; line-height: 1.15;
  }
  .contact {
    position: absolute; left: 60px; width: 280px;
    text-align: center; font-size: 20px;
  }
  .contact--phone { top: 414px; font-size: 24px; }
  .contact--email { top: 477px; font-size: 17px; }
  .contact--address { top: 530px; font-size: 18px; line-height: 1.3; }

  .back-title {
    position: absolute; top: 120px; left: 40px;
    font-size: 54px; line-height: 1.05;
  }
  .badge {
    position: absolute; top: 400px; left: 60px; width: 110px; text-align: center;
  }
  .badge-seal {
    width: 78px; height: 78px; border-radius: 50%;
    background: var(--badge); margin: 0 auto 6px;
  }
  .badge-note { font-size: 11px; color: var(--fine); line-height: 1.2; }
  .partner {
    position: absolute; display: flex; align-items: center; gap: 8px;
    font-size: 30px; color: var(--maroon);
  }
  .partner-mark { width: 18px; height: 18px; background: var(--maroon); }
  .partner-mark--round { border-radius: 50%; }
  .partner--nimbo { top: 395px; left: 240px; }
  .partner--ledgra { top: 490px; left: 240px; }
  .partner--tallyo { top: 560px; left: 60px; }
</style>
</head>
<body>

<section class="card card--front">
  <svg class="card-shapes" width="400" height="660" viewBox="0 0 400 660" aria-hidden="true">
    <polygon class="tab" points="240,0 370,0 370,58 240,46"/>
    <line class="rule" x1="60" y1="400" x2="340" y2="400"/>
    <line class="rule" x1="60" y1="462" x2="340" y2="462"/>
    <line class="rule" x1="60" y1="518" x2="340" y2="518"/>
    <polygon class="tab" points="30,612 170,600 170,660 30,660"/>
  </svg>
  <p class="holder-name">Kim Farrow</p>
  <h1 class="business-name">Bright Ledger<br>Bookkeeping</h1>
  <p class="contact contact--phone">0488 615 903</p>
  <p class="contact contact--email">kim@kimfarrow-example.com.au</p>
  <p class="contact contact--address">PO Box 562 Marlin Reach,<br>Qld 4388</p>
</section>

<section class="card card--back">
  <h2 class="back-title">Bright Ledger<br>Bookkeeping</h2>
  <div class="badge">
    <div class="badge-seal" role="img" aria-label="Registered BAS Agent badge"></div>
    <p class="badge-note">BAS agent<br>42817</p>
  </div>
  <div class="partner partner--nimbo"><span class="partner-mark partner-mark--round"></span>Nimbo</div>
  <div class="partner partner--ledgra"><span class="partner-mark"></span>LEDGRA</div>
  <div class="partner partner--tallyo">Tallyo<span class="partner-mark"></span></div>
</section>

</body>
</html>
```